Kestrel Home Business Card Design

We need a business card for a Building company based in Queensland, Australia. Our colours are orange black and we do base all our homes design names and other aspect of our business on astrology. We want the consumer to perceive the company as professional and to attract investors to our company.We have over 20 years in the building industry.We pride ourselves on our innovation of designs and making the building process for anyone from families to investor a smooth and simple experience.
Business
Amelia Prichard0411752116PO Box 454, Mudgeerbaameliaprichard@zodiachomes.com

```html
<!DOCTYPE html>
<html lang="en">
<head>
<meta charset="utf-8">
<title>Kestrel Homes Business Card</title>
<link rel="stylesheet" href="https://fonts.googleapis.com/css2?family=Lato:wght@400;700;900&display=swap">
<style>
  :root {
    --stage: #2a2a2a;
    --card-white: #ffffff;
    --card-fade: #ececec;
    --orange: #e38a1f;
    --orange-deep: #b4650f;
    --ink: #1b1b1b;
    --navy: #14213d;
    --mist: rgba(120, 120, 120, 0.22);
    --mist-ring: rgba(227, 138, 31, 0.25);
  }
  * { margin: 0; padding: 0; box-sizing: border-box; }
  html, body { width: 1200px; height: 873px; overflow: hidden; }
  body {
    background: var(--stage);
    font-family: "Lato", Arial, sans-serif;
    position: relative;
  }

  /* Back of card */
  .card-back {
    position: absolute;
    left: 70px; top: 200px;
    width: 500px; height: 310px;
    border-radius: 22px;
    background: linear-gradient(180deg, var(--card-fade), var(--card-white));
    overflow: hidden;
  }
  .card-back .faint-mark {
    position: absolute;
    left: 170px; top: -190px;
    width: 320px; height: 320px;
    border-radius: 50%;
    background: var(--mist);
    box-shadow: 0 0 0 30px var(--mist-ring);
  }
  .card-back .brand {
    position: absolute;
    left: 0; right: 0; bottom: 36px;
    display: flex; flex-direction: column; align-items: center; gap: 12px;
  }

  /* Shared brand lockup */
  .brand-dot {
    width: 46px; height: 46px; border-radius: 50%;
    background: var(--orange);
  }
  .brand-name {
    font-weight: 900;
    font-size: 30px;
    color: var(--ink);
    letter-spacing: 0.5px;
  }
  .card-back .brand-dot { width: 38px; height: 38px; }
  .card-back .brand-name { font-size: 24px; }

  /* Front of card */
  .card-front {
    position: absolute;
    left: 640px; top: 70px;
    width: 440px; height: 730px;
    border-radius: 26px;
    background: var(--card-white);
    overflow: hidden;
    display: flex; flex-direction: column;
  }
  .card-front .header {
    height: 205px;
    display: flex; flex-direction: column; align-items: center; justify-content: center; gap: 18px;
  }
  .card-front .brand-dot { width: 70px; height: 70px; }
  .card-front .band {
    height: 395px;
    background: linear-gradient(170deg, var(--orange), var(--orange-deep));
    padding: 55px 0 0 0;
    position: relative;
  }
  .person { text-align: center; }
  .person-name {
    font-weight: 900; font-size: 34px; color: var(--card-white); letter-spacing: 0.5px;
  }
  .person-role {
    font-weight: 900; font-size: 18px; color: var(--navy); letter-spacing: 2px; margin-top: 2px;
  }
  .contacts {
    list-style: none;
    margin: 95px 0 0 60px;
    display: flex; flex-direction: column; gap: 28px;
  }
  .contacts li {
    display: flex; align-items: center; gap: 24px;
    font-size: 21px; color: var(--ink); letter-spacing: 0.5px;
  }
  .contacts svg { width: 30px; height: 24px; flex: none; }
  .pin-badge {
    position: absolute; left: 50%; bottom: -22px; transform: translateX(-50%);
    width: 46px; height: 46px; border-radius: 50%;
    background: var(--orange); border: 4px solid var(--card-white);
    display: flex; align-items: center; justify-content: center;
  }
  .pin-badge svg { width: 20px; height: 26px; }
  .card-front .footer {
    flex: 1;
    display: flex; align-items: center; justify-content: center;
    padding-top: 30px;
    font-weight: 700; font-size: 22px; color: var(--orange);
  }
</style>
</head>
<body>

<section class="card-back" aria-label="Business card back">
  <div class="faint-mark"></div>
  <div class="brand">
    <span class="brand-dot"></span>
    <span class="brand-name">Kestrel Homes</span>
  </div>
</section>

<section class="card-front" aria-label="Business card front">
  <header class="header">
    <span class="brand-dot"></span>
    <span class="brand-name">Kestrel Homes</span>
  </header>

  <div class="band">
    <div class="person">
      <div class="person-name">Harriet Colvane</div>
      <div class="person-role">President</div>
    </div>
    <ul class="contacts">
      <li>
        <svg viewBox="0 0 30 24" aria-hidden="true">
          <path d="M2 7c0-3 5-5 13-5s13 2 13 5v2h-6V6H8v3H2z" fill="#1b1b1b"/>
          <path d="M7 11h16l4 11H3z" fill="#1b1b1b"/>
          <circle cx="15" cy="16" r="3" fill="#e38a1f"/>
        </svg>
        <span>0487309625</span>
      </li>
      <li>
        <svg viewBox="0 0 30 24" aria-hidden="true">
          <rect x="1" y="3" width="28" height="18" fill="#1b1b1b"/>
          <path d="M2 4l13 10L28 4" fill="none" stroke="#c7781a" stroke-width="1.6"/>
        </svg>
        <span>reid@kestrelhomes.example</span>
      </li>
    </ul>
    <div class="pin-badge">
      <svg viewBox="0 0 20 26" aria-hidden="true">
        <path d="M10 1a8 8 0 0 0-8 8c0 6 8 16 8 16s8-10 8-16a8 8 0 0 0-8-8z" fill="#1b1b1b"/>
        <circle cx="10" cy="9" r="3" fill="#ffffff"/>
      </svg>
    </div>
  </div>

  <footer class="footer">PO Box 872, Corvale</footer>
</section>

</body>
</html>
```